Business Card Design For Office Furniture Clearance Company

Kestrel Office Clearance - our company name pretty much explains what we do, we clear offices for high end clients, mainly plc's and large international companies.

We require a nice looking business card that displays professionalism but without being too serious.

It would be nice to see just a little more than a conventional boring business card, make sure you add some flare.

Industry/Entity Type

Office Furniture

Contact Information for Business Card

CARD 1

Mark Holloway
Director
mark@kestrelofficeclearance.co.uk
m: 07700 153928

t: 01632 960418
www.kestrelofficeclearance.co.uk

Kestrel Office Clearance
Unit K4 B
2-8 Fenwick Lane
Ashcombe
Northvale
ZZ9 4QT

free office clearances… you cant get better than that.

CARD 2

Peter Radford
Director
peter@kestrelofficeclearance.co.uk
m: 07700 382615

t: 01632 960418

Kestrel Office Clearance
Unit K4 B
2-8 Fenwick Lane
Ashcombe
Northvale
ZZ9 4QT

Font styles to use
Sans Serif

Requirements
Must have
• A white background - as we have a blue logo.
Nice to have
• Nice use of the logo - play around with this and dissect it.

```html
<!DOCTYPE html>
<html lang="en">
<head>
<meta charset="utf-8">
<title>Kestrel Office Clearance – Business Card</title>
<link href="https://fonts.googleapis.com/css2?family=Open+Sans:wght@400;600;700&display=swap" rel="stylesheet">
<style>
  :root {
    --page-bg: #e9eaec;
    --brand-blue: #1b8ad3;
    --brand-blue-dark: #0b66aa;
    --brand-blue-light: #4aa9e6;
    --charcoal: #3d3f42;
    --text-grey: #5b5e63;
    --card-white: #ffffff;
    --card-shade: #eceef0;
  }
  * { box-sizing: border-box; margin: 0; padding: 0; }
  html, body {
    width: 1200px; height: 843px; overflow: hidden;
    background: var(--page-bg);
    font-family: "Open Sans", Arial, sans-serif;
  }
  .layout {
    width: 1200px; height: 843px;
    display: flex; align-items: center; justify-content: center; gap: 40px;
  }
  .card {
    position: relative; width: 540px; height: 350px; overflow: hidden;
    border-radius: 4px;
    box-shadow: 0 12px 30px rgba(0,0,0,.18);
  }

  /* Back of card */
  .card-back {
    background: linear-gradient(160deg, var(--brand-blue-light) 0%, var(--brand-blue) 45%, var(--brand-blue-dark) 100%);
  }
  .back-mark {
    position: absolute; left: 180px; top: 60px; width: 180px; height: 180px;
    border-radius: 50%; background: var(--card-white);
    display: flex; align-items: center; justify-content: center; text-align: center;
    color: var(--brand-blue); font-weight: 700; font-size: 20px; line-height: 1.2;
  }
  .tagline {
    position: absolute; left: 0; right: 0; bottom: 42px; text-align: center;
    color: var(--card-white); font-size: 15px; font-weight: 400; letter-spacing: .2px;
  }

  /* Front of card */
  .card-front {
    background: linear-gradient(180deg, var(--card-white) 0%, var(--card-white) 55%, var(--card-shade) 100%);
  }
  .company-block { position: absolute; left: 40px; top: 28px; }
  .company-name { color: var(--brand-blue); font-weight: 700; font-size: 17px; }
  .address { color: var(--text-grey); font-size: 14px; line-height: 1.3; margin-top: 2px; }

  .name-band {
    position: absolute; left: 0; top: 140px; width: 420px; height: 56px;
    background: linear-gradient(90deg, var(--brand-blue) 0%, var(--brand-blue-light) 100%);
    padding: 6px 0 0 40px; color: var(--card-white);
  }
  .person-name { font-size: 21px; font-weight: 600; letter-spacing: .5px; line-height: 1.15; }
  .person-role { font-size: 13px; letter-spacing: .6px; }

  .tail-band {
    position: absolute; left: 400px; top: 178px; width: 140px; height: 52px;
    background: var(--charcoal);
  }
  .badge {
    position: absolute; left: 330px; top: 128px; width: 140px; height: 140px;
    border-radius: 50%; background: var(--brand-blue);
    border: 6px solid var(--card-white);
    display: flex; align-items: center; justify-content: center; text-align: center;
    color: var(--card-white); font-weight: 700; font-size: 15px; line-height: 1.2;
  }

  .contact-list { position: absolute; left: 40px; top: 214px; list-style: none; }
  .contact-list li {
    display: flex; align-items: center; gap: 10px;
    color: var(--text-grey); font-size: 14px; height: 23px;
  }
  .contact-list svg { width: 14px; height: 14px; fill: var(--brand-blue); flex: none; }
</style>
</head>
<body>
<main class="layout">

  <section class="card card-back" aria-label="Card back">
    <div class="back-mark">Kestrel<br>Office<br>Clearance</div>
    <p class="tagline">No-cost office clearances… it’s hard to beat that.</p>
  </section>

  <section class="card card-front" aria-label="Card front">
    <div class="company-block">
      <p class="company-name">Kestrel Office Clearance</p>
      <p class="address">Unit K4 B, 2-8 Fenwick Lane<br>Ashcombe, Northvale<br>ZZ9 4QT</p>
    </div>

    <div class="name-band">
      <p class="person-name">MARK HOLLOWAY</p>
      <p class="person-role">DIRECTOR</p>
    </div>
    <div class="tail-band"></div>
    <div class="badge">Kestrel<br>Office<br>Clearance</div>

    <ul class="contact-list">
      <li>
        <svg viewBox="0 0 24 24" aria-hidden="true"><path d="M6.6 10.8a15.1 15.1 0 0 0 6.6 6.6l2.2-2.2c.3-.3.7-.4 1-.2 1.1.4 2.3.6 3.6.6.6 0 1 .4 1 1V20c0 .6-.4 1-1 1A17 17 0 0 1 3 4c0-.6.4-1 1-1h3.5c.6 0 1 .4 1 1 0 1.3.2 2.5.6 3.6.1.3 0 .7-.2 1z"/></svg>
        01632 960418
      </li>
      <li>
        <svg viewBox="0 0 24 24" aria-hidden="true"><path d="M7 1h10a2 2 0 0 1 2 2v18a2 2 0 0 1-2 2H7a2 2 0 0 1-2-2V3a2 2 0 0 1 2-2zm0 3v14h10V4zm5 15.2a1.2 1.2 0 1 0 0 2.4 1.2 1.2 0 0 0 0-2.4z"/></svg>
        07700 153928
      </li>
      <li>
        <svg viewBox="0 0 24 24" aria-hidden="true"><path d="M2 5h20v14H2zm2 2v.5l8 5 8-5V7zm0 3v7h16v-7l-8 5z"/></svg>
        mark@kestrelofficeclearance.co.uk
      </li>
      <li>
        <svg viewBox="0 0 24 24" aria-hidden="true"><path d="M12 2a10 10 0 1 0 0 20 10 10 0 0 0 0-20zm6.9 9h-3a15 15 0 0 0-1.3-5.6A8 8 0 0 1 18.9 11zM12 4.1c.9 1.2 1.8 3.6 1.9 6.9h-3.8c.1-3.3 1-5.7 1.9-6.9zM9.4 5.4A15 15 0 0 0 8.1 11h-3a8 8 0 0 1 4.3-5.6zM5.1 13h3a15 15 0 0 0 1.3 5.6A8 8 0 0 1 5.1 13zm6.9 6.9c-.9-1.2-1.8-3.6-1.9-6.9h3.8c-.1 3.3-1 5.7-1.9 6.9zm2.6-1.3a15 15 0 0 0 1.3-5.6h3a8 8 0 0 1-4.3 5.6z"/></svg>
        www.kestrelofficeclearance.co.uk
      </li>
    </ul>
  </section>

</main>
</body>
</html>
```